Business Card Design

New business card design

Target Market(s)

Residential & Commercial Property Managers

Industry/Entity Type

Plumbing Services

Contact Information for Business Card

Name - Rowan Keddle, title - Director, Phone Number - 0431 286 517, email - rowan@tbk-plumbing.com.au, Company ABN - 73 215 904 386,

Font styles to use
Sans Serif

Colors
0054AA
0677BA
7BADD7
CADEEF
E8F1F8

```html
<!DOCTYPE html>
<html lang="en">
<head>
<meta charset="utf-8">
<title>TBK Plumbing Services – Business Card</title>
<link rel="stylesheet" href="https://fonts.googleapis.com/css2?family=Montserrat:wght@400;500;600;700&display=swap">
<style>
  :root {
    --backdrop: #8d7256;
    --card-white: #ffffff;
    --ink: #1e2630;
    --ink-soft: #2b3440;
    --brand-blue: #29a8e0;
    --shadow: rgba(0, 0, 0, 0.35);
  }
  * { box-sizing: border-box; margin: 0; padding: 0; }
  html, body {
    width: 900px; height: 1200px; overflow: hidden;
    background: var(--backdrop);
    font-family: "Montserrat", sans-serif;
    color: var(--ink);
  }
  .canvas { position: relative; width: 900px; height: 1200px; }
  .card {
    position: absolute; border-radius: 24px; overflow: hidden;
    box-shadow: 0 6px 14px var(--shadow);
  }
  .card--front { left: 80px; top: 130px; width: 742px; height: 442px; background: var(--card-white); }
  .card--back { left: 78px; top: 638px; width: 744px; height: 440px; background: var(--brand-blue); }

  .brand-name {
    position: absolute; font-weight: 600; color: var(--ink);
    white-space: nowrap; letter-spacing: 0.5px;
  }
  .card--front .brand-name { left: 50px; top: 196px; font-size: 25px; width: 290px; text-align: center; }
  .card--back .brand-name { left: 0; width: 744px; top: 196px; font-size: 46px; text-align: center; }

  .divider { position: absolute; left: 367px; top: 128px; width: 2px; height: 180px; background: var(--ink); }

  .contact { position: absolute; left: 388px; top: 124px; }
  .contact__name { font-size: 24px; font-weight: 700; line-height: 1.2; }
  .contact__title { font-size: 15px; font-weight: 400; margin-top: 2px; }
  .contact__list { list-style: none; margin-top: 20px; }
  .contact__item {
    display: flex; align-items: center; gap: 10px;
    font-size: 15.5px; font-weight: 400; height: 30px;
  }
  .contact__item svg { width: 17px; height: 17px; fill: var(--ink); flex: none; }
  .contact__item strong { font-weight: 700; }

  .band { position: absolute; left: 0; top: 376px; width: 742px; height: 31px; }
</style>
</head>
<body>
<main class="canvas">
  <section class="card card--front">
    <div class="brand-name">TBK Plumbing Services</div>
    <div class="divider"></div>
    <div class="contact">
      <div class="contact__name">Rowan Keddle</div>
      <div class="contact__title">Director</div>
      <ul class="contact__list">
        <li class="contact__item">
          <svg viewBox="0 0 24 24" aria-hidden="true"><path d="M6.6 10.8a15.1 15.1 0 0 0 6.6 6.6l2.2-2.2c.3-.3.7-.4 1-.2 1.1.4 2.3.6 3.6.6.6 0 1 .4 1 1V20c0 .6-.4 1-1 1A17 17 0 0 1 3 4c0-.6.4-1 1-1h3.5c.6 0 1 .4 1 1 0 1.3.2 2.5.6 3.6.1.3 0 .7-.2 1z"/></svg>
          <span>0431 286 517</span>
        </li>
        <li class="contact__item">
          <svg viewBox="0 0 24 24" aria-hidden="true"><path d="M3 5h18v14H3z M3 6l9 6 9-6" fill="none" stroke="currentColor"/><path d="M3 5h18v2l-9 6-9-6z"/><path d="M3 8.5l9 6 9-6V19H3z"/></svg>
          <span>rowan@tbk-plumbing.com.au</span>
        </li>
        <li class="contact__item">
          <svg viewBox="0 0 24 24" aria-hidden="true"><circle cx="12" cy="12" r="9" fill="none" stroke="#1e2630" stroke-width="2"/><path d="M12 3a9 9 0 0 1 0 18M3 12h18" fill="none" stroke="#1e2630" stroke-width="2"/></svg>
          <span>www.tbk-plumbing.com.au</span>
        </li>
        <li class="contact__item">
          <span><strong>ABN</strong> - 73 215 904 386</span>
        </li>
      </ul>
    </div>
    <svg class="band" viewBox="0 0 742 31" aria-hidden="true">
      <rect x="0" y="0" width="345" height="31" fill="#1e2630"/>
      <rect x="398" y="0" width="344" height="31" fill="#29a8e0"/>
      <circle cx="369" cy="10" r="31" fill="#ffffff"/>
      <circle cx="369" cy="10" r="22" fill="#29a8e0"/>
    </svg>
  </section>

  <section class="card card--back">
    <div class="brand-name">TBK Plumbing Services</div>
  </section>
</main>
</body>
</html>
```